Small Business Directory Site Requires a Professional Responsive Web Design

Small Business Directory and Coupon Site - we require a complete website design for a brand new responsive & mobile friendly website. We already have a coder who will professional code our website in Magento.

All PSD pages need to be professionally designed then uploaded into a sharedrive (i.e. like filecrate). Additionally, as I cannot pre-empt everything, please note that we may require a little more assistance once the files have been transferred (for example, in www.brightlane-listings.example if you hover your mouse on the search box you will see a pop up box. We want one of these too and I think that means there may be extra design work here)

We have some draft page sketches have been created (there are some minor changes we want to the sketches provided though); however, we require an excellent designer to add the creative touches to it to make it look professionally created. All artwork/font must be legal.

-------------------------
We like the look of the www.brightlane-listings.example and www. marlowfolio.example

For the headers, please consider a font similar to RNS camellia. We likes this style, but it is too thin for the headers...so we need a variation like this one. For the copy/general text font, something basic that marries well with the headers.

---------------------

Please be sure to also read the brief we wrote for the coder as this will help with better understanding our design requirements.

In total I believe we have about 50 pages. This includes all the little pages and most of the pop up boxes (but not the little help key boxes). For example, pages include...

1. Login (this is where customers log in and can edit, manage their profiles. This means that there are backend membership pages)
2. Mini Services (same look and feel as the business coupons)
3. Resource Centre
4. Join (this is where customers learn about the packages available to submit a directory listing, if they ‘buy’ a package (i.e. free, $25 or $150 package) then they can create their own directory listing)
5. Search the directory (customer can view all the categories and also search the directory)
6. Create a directory listing (this is where customers learn about the packages available to submit a directory listing, if they ‘buy’ a package (i.e. free, $25 or $150 package) then they can create their own directory listing)
7. Quote finder (also know as Get a Quote)
8. Coupons (customer go to the business coupon page and can view all current coupons/submit a coupon)
9. Submit a coupon (form)
10.Advertise with us (form)
11. Join the forum
12.Submit an article or video (form)
13. Affiliates (listing of affiliates we currently have)
14. Become an affiliate (form)
15. Case studies (customer can view the case studies we have in the resource centre)
16. Help Guides (customer can view the help guides we have in the resource centre)
17. About Us
18 .Contact Us (form)
19. Terms & Condition
20. Privacy Policy
21. Supporting City Councils
22. Site Map
23. Forgot password / login details
24. Homepage
25. If we hover over a few areas (i.e. search box, location field) it pops up with more information.
etc etc etc. . . there are more pages.

Please see our filecrate link for the draft mock up pages that I have created so far.

https://www.cloudtrunk.example/sh/qk72pmw4rtz8nd/KLMvbTq2fWndxPzs8Yh4ecRQu

We are in a rush! We'd like to get the majority of the artwork completed by the end of the month. Minor fixes/tweaks can occur thereafter.

Target Market(s)

Small Businesses (employees 0 - 50) located throughout Australia

Industry/Entity Type

Business

Font styles to use
Sans Serif

Requirements
Must have
• Professional. Artwork must be legal (cannot be cut and paste or taken off other websites, must be legally purchased and used).Must look contemporary, fresh, modern.

Absolutely must be a responsive site!
Nice to have
• original work, original photos, original art.

like modern, fresh photos that demonstrate innovation, growth, small business, Australian scenery, stability, goals/passion.
Should not have
• cut and paste graphics, illegal graphics, not purchased graphics.

```html
<!DOCTYPE html>
<html lang="en">
<head>
<meta charset="utf-8">
<title>Harbour Trade Link</title>
<link href="https://fonts.googleapis.com/css2?family=Open+Sans:wght@400;600;700&family=Arimo:wght@400;700&display=swap" rel="stylesheet">
<style>
:root{
  --black:#050505;
  --footer-base:#161616;
  --orange:#e07a2c;
  --white:#ffffff;
  --ink:#333333;
  --muted:#6a6a6a;
  --link:#9a9a9a;
  --field:#1c1c1c;
  --partner:#7d7d7d;
}
*{margin:0;padding:0;box-sizing:border-box}
html,body{width:949px;height:1200px;overflow:hidden;background:var(--white)}
body{position:relative;font-family:"Open Sans",sans-serif;color:var(--ink)}
.abs{position:absolute}

/* header */
.site-header{left:0;top:0;width:949px;height:97px;background:var(--black)}
.brand{left:106px;top:34px;display:flex;align-items:center;gap:8px;color:var(--white);font-size:18px;font-weight:600;letter-spacing:.3px}
.brand-mark{width:12px;height:12px;background:var(--orange)}
.search-field{top:33px;height:34px;background:var(--field);color:#ddd;font-size:9px;line-height:34px;padding-left:10px}
.search-what{left:344px;width:143px}
.search-near{left:502px;top:33px;line-height:34px;color:#eee;font-size:13px}
.search-where{left:540px;width:142px}
.search-btn{left:690px;top:33px;width:36px;height:34px;background:var(--field);display:flex;align-items:center;justify-content:center}
.nav-link{top:33px;line-height:34px;color:var(--white);font-size:12px;font-weight:600}

/* hero */
.hero{left:0;top:97px;width:949px;height:403px;background:linear-gradient(180deg,#3a2a16 0%,#a06a20 30%,#c88a2a 45%,#4a3418 62%,#8a6a32 80%,#a68446 100%)}
.hero-title{left:110px;top:232px;color:var(--white);font-size:33px;font-weight:700;letter-spacing:.5px}
.hero-sub{left:110px;top:280px;color:var(--white);font-size:21px;font-weight:700}
.hero-btn{left:112px;top:327px;width:193px;height:38px;background:var(--orange);color:var(--white);font-size:13px;text-align:center;line-height:38px}
.directory-panel{left:610px;top:172px;width:213px;height:250px;background:rgba(40,40,40,.62);text-align:center;color:var(--white)}
.directory-panel h2{font-size:23px;font-weight:600;margin-top:18px;letter-spacing:.5px}
.directory-panel p{font-size:9.5px;line-height:20px;margin:10px 14px 0}
.listing-btn{display:inline-block;margin-top:14px;width:164px;height:35px;line-height:35px;background:#111;font-size:10.5px}
.panel-arrows{display:flex;justify-content:center;gap:8px;margin-top:13px}
.panel-arrows span{width:14px;height:14px;border-radius:50%;background:#444}
.slide-dots{left:436px;top:469px;display:flex;gap:7px}
.slide-dots span{width:10px;height:10px;border-radius:2px;background:#ddd}
.slide-dots span.active{background:var(--orange)}

/* community */
.section-title{left:0;top:525px;width:949px;text-align:center;color:var(--orange);font-size:20px;font-weight:600}
.card-frame{top:571px;width:241px;height:155px;border:1px solid #ddd;padding:4px;background:#fff}
.card-media{width:100%;height:100%}
.card-name{display:flex;align-items:center;justify-content:center;gap:10px;background:#fff;color:#1f3f86;font-size:26px;font-weight:700}
.card-name i{width:30px;height:30px;border-radius:50%;background:#2a9be0;display:block}
.card-title{top:736px;font-size:12px;color:#333}
.card-text{top:760px;width:230px;font-size:9px;line-height:16.5px;color:var(--muted)}

.divider{left:110px;top:838px;width:730px;height:8px;background:radial-gradient(ellipse at top,rgba(0,0,0,.18),rgba(0,0,0,0) 70%)}
.partner{top:880px;width:170px;text-align:center;color:var(--partner);font-size:32px;font-weight:700;font-family:"Arimo",sans-serif}

/* footer */
.site-footer{left:0;top:965px;width:949px;height:187px;background:var(--black)}
.footer-col{top:985px}
.footer-col h3{color:var(--white);font-size:11px;font-weight:700;font-family:"Arimo",sans-serif;margin-bottom:9px}
.footer-col li{list-style:none;color:var(--link);font-family:"Arimo",sans-serif;font-size:9px;line-height:19.3px}
.social{display:flex;gap:4px;margin-top:16px}
.social span{width:22px;height:22px;border-radius:50%;background:#bfbfbf}
.footer-base{left:0;top:1152px;width:949px;height:48px;background:var(--footer-base);color:#ccc;font-family:"Arimo",sans-serif;font-size:9px;text-align:center;line-height:48px}
</style>
</head>
<body>

<header class="abs site-header">
  <div class="abs brand"><span class="brand-mark"></span>Harbour Trade Link</div>
  <div class="abs search-field search-what">What Do You Want To Find?</div>
  <div class="abs search-near">Near</div>
  <div class="abs search-field search-where">Chennai,25</div>
  <div class="abs search-btn">
    <svg width="12" height="12" viewBox="0 0 12 12"><circle cx="5" cy="5" r="3.6" fill="none" stroke="#fff" stroke-width="1.8"/><line x1="7.6" y1="7.6" x2="11" y2="11" stroke="#fff" stroke-width="2"/></svg>
  </div>
  <div class="abs nav-link" style="left:757px">LOGIN</div>
  <div class="abs nav-link" style="left:820px">JOIN</div>
</header>

<section class="abs hero" role="img" aria-label="Sunset over a grassy plain with birds in flight"></section>
<h1 class="abs hero-title">LET US HELP YOU GROW</h1>
<p class="abs hero-sub">AUSTRALIA’S SMALL BUSINESS SUPPORT LINK</p>
<div class="abs hero-btn">JOIN HARBOUR TRADE LINK</div>
<aside class="abs directory-panel">
  <h2>DIRECTORY</h2>
  <p>Our small business directory is maitained to give members choice. We’re open toall businesses, regardless of your location,so long as they service Australian small businesses.</p>
  <div class="listing-btn">CREATE YOUR FREE LISTING</div>
  <div class="panel-arrows"><span></span><span></span></div>
</aside>
<div class="abs slide-dots"><span class="active"></span><span></span><span></span><span></span></div>

<h2 class="abs section-title">GET REAL SUPPORT FROM OUR COMMUNITY</h2>

<div class="abs card-frame" style="left:103px"><div class="card-media" role="img" aria-label="Business meeting desk with charts and coffee" style="background:linear-gradient(135deg,#d9dde2,#9aa4ad 60%,#cfd5da)"></div></div>
<div class="abs card-frame" style="left:355px"><div class="card-media" role="img" aria-label="Support staff at a call centre, video thumbnail with play button" style="background:linear-gradient(135deg,#9aa3ac,#c9b6a6 50%,#7e8a96);display:flex;align-items:center;justify-content:center"><svg width="40" height="40" viewBox="0 0 40 40"><circle cx="20" cy="20" r="18" fill="none" stroke="#fff" stroke-width="2.5"/><path d="M16 12 L28 20 L16 28 Z" fill="#fff"/></svg></div></div>
<div class="abs card-frame" style="left:604px"><div class="card-media card-name"><i></i>Keystone Cover</div></div>

<h3 class="abs card-title" style="left:104px">HOW DID YOU SORT YOUR BUSINESS?</h3>
<h3 class="abs card-title" style="left:355px">WHY GO WITH HARBOUR TRADE LINK?</h3>
<h3 class="abs card-title" style="left:605px">BECOME AN AFFILIATE</h3>
<p class="abs card-text" style="left:104px">Learn from Lena Marsh, a real small business owner. How she started her business and what are the most valuable resourcesfor her right now</p>
<p class="abs card-text" style="left:355px">What small business owner can’t relate to the ongoing task of attracting new customers? Struggling with cash flow? Or how about not having enough time in the day</p>
<p class="abs card-text" style="left:605px">If you have a network of small businesses, let us help to create additional value for your members and make money Talk to us today about how we can help.</p>

<div class="abs divider"></div>
<div class="abs partner" style="left:110px">Granfield</div>
<div class="abs partner" style="left:298px">Plannova</div>
<div class="abs partner" style="left:480px">Norvex</div>
<div class="abs partner" style="left:665px">Granfield</div>

<footer class="abs site-footer"></footer>
<div class="abs footer-col" style="left:104px"><h3>SITE DIRECTORY</h3><ul><li>// News &amp; Articles</li><li>// Find a Business</li><li>// Maps &amp; Directions</li><li>// White Pages</li><li>// Mobile Apps</li><li>// Reverse Phone Lookup</li></ul></div>
<div class="abs footer-col" style="left:255px"><h3>RESOUROES</h3><ul><li>// Join the Forum</li><li>// Submit an Article</li><li>// Affiliates</li><li>// Become an Affiliate</li><li>// Case Studies</li><li>// Help Guides</li></ul></div>
<div class="abs footer-col" style="left:393px"><h3>POPULAR CATEGORES</h3><ul><li>// News &amp; Articles</li><li>// Find a Business</li><li>// Maps &amp; Directions</li><li>// White Pages</li><li>// Mobile Apps</li><li>// Reverse Phone Lookup</li></ul></div>
<div class="abs footer-col" style="left:554px"><h3>ABOUT US</h3><ul><li>// About Us</li><li>// Contact Us</li><li>// Terms &amp; Condition</li><li>// Privacy Polacy</li><li>// Supporting City</li><li>// Site Map</li></ul></div>
<div class="abs footer-col" style="left:689px"><h3>FOLLOW US</h3><div class="social"><span></span><span></span><span></span><span></span><span></span></div></div>
<div class="abs footer-base">© Copy Rights 2014.Harbour Trade Link.All Rights Reserved.</div>

</body>
</html>
```